Stationery Design Project for Marketing Consultancy

I have started a new consultancy business and require the following elements to be designed using existing logo:
• Business card
• Letterhead
• Envelope (DL, C4, C5)
• Microsoft word template for report writing
• A4 Presentation Folder
• Powerpoint template
COPY FOR FRONT AND BACK OF BUSINESS CARD
logo
'Measurable Marketing. Epic Results' slogan (but no need to use existing lockup with logo)
name, B Bus. Mktg, Grad Dip Digital Mktg, CPM (post nominal abbreviations in smaller font)
mobile: 04XX-XXX-XXX (I will give details to the winner to add)
website: www.tolvarin.com.au
email: info@tolvarin.com.au
COPY FOR LETTERHEAD
Logo
Company Name
Please, submit your designs that include business card, letterhead and envelope. Once selected the winner will be asked to complete the project by creating the rest of the artwork.
FINAL FILES
Print ready files to be supplied as well as Indesign files so that minor amends can be made if necessary in future.
• Layered vectors in EPS & PDF
• Screen quality JPEG & PNGs
ABOUT THE BUSINESS: TOLVARIN
I work with clients to understand their business challenges, developing and executing measurable marketing strategies tied to key business metrics. Services include:
Services include:
• Business planning and business development
• Marketing and brand strategy
• Insight-driven integrated campaigns
• Loyalty programs and retention marketing
• Marketing automation
• Direct marketing (traditional and digital)
• Content strategy and development
Hi everyone,
Target Market(s)
Corporate decision makers (heads of marketing, general managers etc) and small to medium sized business owners. Predominately male aged 35+
Industry/Entity Type
Marketing
Requirements
Must have
- BRAND PERSONALITY
The successful design will communicate brand personality. I am a professional, results-driven entrepreneur, but want to show off my creative flair.
MEMORABILITY
Looking for a unique and eye-catching design. Am considering special printing effects (die cuts, letterpress, interactive elements, embossing, foiling etc) or a striking minimalist approach.
Nice to have
- I have a mission that could be incorporated on reverse if room -
Turning insights into actions & passion into profit.
Should not have
- Use of pink or green.

```html
<!DOCTYPE html>
<html lang="en">
<head>
<meta charset="utf-8">
<title>Tolvarin Business Card</title>
<link href="https://fonts.googleapis.com/css2?family=Open+Sans:wght@400;600;700&display=swap" rel="stylesheet">
<style>
  :root {
    --backdrop: #7a5238;
    --card-top: #3b3b3b;
    --card-bottom: #232323;
    --ink: #ececec;
    --ink-soft: #c9c9c9;
    --mark: #e6e6e6;
  }
  html, body {
    margin: 0;
    padding: 0;
    overflow: hidden;
  }
  .canvas {
    position: relative;
    width: 1200px;
    height: 514px;
    background: var(--backdrop);
    overflow: hidden;
    font-family: "Open Sans", Arial, sans-serif;
    color: var(--ink);
  }
  .card {
    position: absolute;
    top: 126px;
    width: 362px;
    height: 241px;
    background: linear-gradient(180deg, var(--card-top) 0%, var(--card-bottom) 100%);
    box-shadow: 0 3px 8px rgba(0, 0, 0, 0.45);
  }
  .card--front { left: 205px; }
  .card--back { left: 617px; }

  /* Front */
  .front-mark {
    position: absolute;
    left: 146px;
    top: 44px;
    width: 78px;
    height: 78px;
  }
  .front-name {
    position: absolute;
    left: 0;
    right: 0;
    top: 142px;
    margin: 0;
    text-align: center;
    font-weight: 600;
    font-size: 38px;
    line-height: 1;
    letter-spacing: 1px;
    color: var(--mark);
  }
  .front-tagline {
    position: absolute;
    left: 0;
    right: 0;
    top: 192px;
    margin: 0;
    text-align: center;
    font-size: 11px;
    letter-spacing: 0.6px;
    color: var(--ink-soft);
  }

  /* Back */
  .back-mark {
    position: absolute;
    right: 20px;
    top: 10px;
    width: 32px;
    height: 32px;
  }
  .back-name {
    position: absolute;
    right: 12px;
    top: 47px;
    margin: 0;
    font-weight: 600;
    font-size: 12px;
    letter-spacing: 0.5px;
    color: var(--mark);
  }
  .contact {
    position: absolute;
    left: 79px;
    top: 82px;
  }
  .contact__company {
    margin: 0 0 16px;
    font-weight: 700;
    font-size: 16px;
    line-height: 20px;
  }
  .contact__line {
    margin: 0;
    font-size: 12px;
    line-height: 17px;
  }
  .contact__web {
    margin: 4px 0 0;
    font-weight: 700;
    font-size: 14px;
    line-height: 18px;
  }
</style>
</head>
<body>
  <div class="canvas">
    <section class="card card--front">
      <svg class="front-mark" viewBox="0 0 78 78" aria-hidden="true">
        <circle cx="39" cy="39" r="39" fill="var(--mark)"/>
      </svg>
      <p class="front-name">TOLVARIN</p>
      <p class="front-tagline">MEASURABLE MARKETING</p>
    </section>

    <section class="card card--back">
      <svg class="back-mark" viewBox="0 0 32 32" aria-hidden="true">
        <circle cx="16" cy="16" r="16" fill="var(--mark)"/>
      </svg>
      <p class="back-name">TOLVARIN</p>
      <div class="contact">
        <p class="contact__company">Company Name</p>
        <p class="contact__line">M xxx xxx xxxx</p>
        <p class="contact__line">E info@tolvarin.com.au</p>
        <p class="contact__web">www.tolvarin.com.au</p>
      </div>
    </section>
  </div>
</body>
</html>
```